Northfield Builders Guild Business card

We are looking for a new business card design with photo included.
Our business is a nonprofit construction contractor membership organization. We offer business education, assist with business setup and licensing, provide safety training, and provide a member directory.
URL: www.builderslinkguild.org
Color code:
CMYK: 0 cyan, 42 magenta, 100 yellow, 0 black for Print.
Hexidecimal: #FF9900
RGB: R 255; G 153; B 0

```html
<!DOCTYPE html>
<html lang="en">
<head>
<meta charset="utf-8">
<title>Northfield Builders Guild – Business Card</title>
<link rel="stylesheet" href="https://fonts.googleapis.com/css2?family=Jost:wght@400;600;700&display=swap">
<style>
  :root {
    --backdrop: #e4e4e4;
    --card-white: #ffffff;
    --charcoal: #333233;
    --charcoal-deep: #2b2a2b;
    --text-grey: #4a4a4a;
    --orange: #ff9900;
    --band-orange: #f7941d;
    --photo-bg: #f4f6f8;
    --photo-edge: #c9ccd0;
    --logo-muted: #6f6d6e;
  }
  * { margin: 0; padding: 0; box-sizing: border-box; }
  html, body {
    width: 1200px; height: 1200px; overflow: hidden;
    background: var(--backdrop);
    font-family: "Jost", "Futura", sans-serif;
  }
  .canvas { position: relative; width: 1200px; height: 1200px; }

  .card { position: absolute; left: 262px; width: 686px; height: 392px; overflow: hidden; }
  .card--front { top: 165px; background: var(--card-white); }
  .card--back { top: 653px; background: var(--charcoal); }

  .wordmark {
    position: absolute; left: 46px; top: 58px;
    display: flex; align-items: center; gap: 12px;
  }
  .wordmark__square { width: 18px; height: 18px; background: var(--orange); flex: none; }
  .wordmark__name {
    font-weight: 700; font-size: 30px; line-height: 32px;
    letter-spacing: 0.5px; color: var(--charcoal); text-transform: uppercase;
    white-space: nowrap;
  }

  .contact {
    position: absolute; left: 46px; color: var(--text-grey);
    font-size: 16.5px; line-height: 19.5px; font-weight: 400;
    white-space: nowrap;
  }
  .contact--address { top: 176px; }
  .contact--phones { top: 251px; }
  .contact--web { top: 327px; left: 41px; font-size: 16px; }

  .portrait {
    position: absolute; left: 432px; top: 40px; width: 196px; height: 246px;
    border-radius: 12px; border: 1px solid var(--photo-edge);
    background: linear-gradient(180deg, var(--photo-bg) 0%, #dfe2e6 100%);
  }

  .person {
    position: absolute; left: 400px; width: 260px; text-align: center;
    white-space: nowrap;
  }
  .person__name {
    top: 312px; font-weight: 600; font-size: 24px; line-height: 28px;
    color: var(--charcoal); letter-spacing: 0.3px;
  }
  .person__title { top: 342px; font-size: 16.5px; line-height: 20px; color: var(--band-orange); }

  .band { position: absolute; left: 0; bottom: 0; height: 15px; }
  .band--orange { width: 348px; background: var(--band-orange); }
  .band--dark { left: 348px; width: 338px; background: var(--charcoal-deep); }

  .back-mark {
    position: absolute; left: 0; right: 0; top: 138px;
    display: flex; justify-content: center; align-items: center; gap: 16px;
  }
  .back-mark__square { width: 22px; height: 22px; background: var(--orange); flex: none; }
  .back-mark__name {
    font-weight: 700; font-size: 40px; line-height: 44px;
    color: var(--logo-muted); text-transform: uppercase; letter-spacing: 0.5px;
    white-space: nowrap;
  }
</style>
</head>
<body>
<main class="canvas">
  <section class="card card--front">
    <div class="wordmark">
      <span class="wordmark__square"></span>
      <span class="wordmark__name">Northfield<br>Builders Guild</span>
    </div>

    <p class="contact contact--address">2450 NW Alder Ridge Rd.,<br>Suite #210<br>Salem, OR 97301</p>
    <p class="contact contact--phones">P. (555) 214-3870<br>C. 555.302.1946<br>hello@nbguild.org</p>
    <p class="contact contact--web">www.builderslinkguild.org</p>

    <div class="portrait" role="img" aria-label="Portrait photo of the card holder"></div>
    <p class="person person__name">DANIEL HARPER</p>
    <p class="person person__title">President</p>

    <div class="band band--orange"></div>
    <div class="band band--dark"></div>
  </section>

  <section class="card card--back">
    <div class="back-mark">
      <span class="back-mark__square"></span>
      <span class="back-mark__name">Northfield<br>Builders Guild</span>
    </div>
  </section>
</main>
</body>
</html>
```